Logo and bag for Turkish coffee brand

We are a coffee roasting company. We need a logo for our new Turkish coffee brand. We are targeting C+ to A- customer segment. Our brand is above average in pricing and can be expressed as very good in quality or a bit less than excellentOur brand name is قهواكQahwakIt is an Arabic word that means "Your coffee" and if read in a different way it means "I love You"

Target Market(s)

We are selling in Egyptian market for customer segments from C+ and up to A-

Logo Text

Binnitak بنّيتك

Requirements
Must have
• 1. The logo must contain brand name in Arabic good to have it in Arabic and English if possible.
• 2. All text content must be in Arabic and good to be in both Arabic and English
• 3. The package must include two spaces for limited text paragraphs
• an area for production date and expiry.
• 4. An area for selecting variants of the product. Our coffee has light-medium-dark roasted (فاتح - وسط - غامق)
• Plain or flavored (سادة - محوج)

```html
<!DOCTYPE html>
<html lang="en">
<head>
<meta charset="utf-8">
<title>Binnitak Turkish Coffee Bag</title>
<link rel="stylesheet" href="https://fonts.googleapis.com/css2?family=Cairo:wght@400;700&family=Open+Sans:wght@400;600&family=Patrick+Hand&display=swap">
<style>
  :root {
    --backdrop: #e9e4da;
    --bag-black: #2a2a2b;
    --bag-black-deep: #1e1e1f;
    --side-black: #171718;
    --band-red: #a8222a;
    --band-red-deep: #861a20;
    --gold: #b8935a;
    --gold-light: #d9b77c;
    --text-light: #f2f2f2;
    --text-muted: #c9c9c9;
    --label-red: #c0222c;
  }
  * { margin: 0; padding: 0; box-sizing: border-box; }
  html, body {
    width: 1200px; height: 789px; overflow: hidden;
    background: var(--backdrop);
  }
  .canvas { position: relative; width: 1200px; height: 789px; }

  .bag { position: absolute; left: 350px; top: 30px; width: 490px; height: 729px;
    display: flex; box-shadow: 0 6px 24px rgba(0,0,0,0.18); }

  /* side gusset */
  .bag-side {
    position: relative; width: 130px; height: 100%;
    background: var(--side-black); overflow: hidden;
    border-right: 1px solid #0e0e0e;
  }
  .side-band {
    position: absolute; left: 0; top: 0; width: 100%; height: 200px;
    background: linear-gradient(135deg, var(--band-red-deep) 0%, #6e1419 100%);
  }
  .side-rule { position: absolute; left: 0; top: 200px; width: 100%; height: 6px; background: var(--gold); }
  .side-content {
    position: absolute; left: 10px; right: 10px; top: 214px; bottom: 14px;
    display: flex; flex-direction: column; gap: 12px; color: var(--text-light);
  }
  .side-brand {
    font-family: "Cairo", sans-serif; font-weight: 700; font-size: 26px;
    line-height: 1.1; text-align: center;
  }
  .side-para {
    font-size: 10px; line-height: 1.45; color: var(--text-muted);
  }
  .side-para.ar { font-family: "Cairo", sans-serif; text-align: right; }
  .side-para.en { font-family: "Open Sans", sans-serif; }
  .side-heading {
    font-family: "Cairo", sans-serif; font-weight: 700; font-size: 11px;
    text-align: right; color: var(--gold-light); margin-bottom: 3px;
  }
  .option-list { list-style: none; display: flex; flex-direction: column; gap: 2px; }
  .option {
    display: flex; align-items: center; justify-content: flex-end; gap: 6px;
    font-family: "Cairo", sans-serif; font-size: 11px; line-height: 1.3;
  }
  .tick-box {
    width: 11px; height: 11px; border: 1px solid var(--text-light); display: block;
  }
  .date-field { display: flex; flex-direction: column; gap: 6px; }
  .date-row {
    display: flex; align-items: flex-end; justify-content: space-between; gap: 6px;
    font-size: 10px;
  }
  .date-row .en { font-family: "Open Sans", sans-serif; font-weight: 600; }
  .date-row .ar { font-family: "Cairo", sans-serif; }
  .date-line { display: block; height: 14px; border-bottom: 1px solid var(--text-muted); margin-top: 2px; }

  /* front panel */
  .bag-front {
    position: relative; width: 360px; height: 100%;
    background: linear-gradient(160deg, var(--bag-black) 0%, var(--bag-black-deep) 100%);
    overflow: hidden;
  }
  .pattern-band {
    position: absolute; left: 0; top: 0; width: 100%; height: 200px;
    background: linear-gradient(135deg, var(--band-red) 0%, var(--band-red-deep) 100%);
  }
  .gold-rule { position: absolute; left: 0; top: 200px; width: 100%; height: 6px; background: var(--gold); }
  .brand-name {
    position: absolute; left: 0; top: 214px; width: 100%; text-align: center;
    font-family: "Cairo", sans-serif; font-weight: 700; font-size: 60px; line-height: 1.1;
    color: var(--text-light);
  }
  .brand-tagline {
    position: absolute; left: 0; top: 298px; width: 100%; text-align: center;
    font-family: "Patrick Hand", cursive; font-size: 26px; letter-spacing: 1px;
    color: var(--text-light);
  }
  .product-illustration {
    position: absolute; left: 105px; top: 365px; width: 150px; height: 155px; display: block;
  }
  .product-title {
    position: absolute; left: 0; top: 535px; width: 100%;
    display: flex; align-items: center; justify-content: center; gap: 10px;
    font-family: "Open Sans", sans-serif; font-size: 26px; line-height: 1.2;
    color: var(--text-light); letter-spacing: 1px;
  }
  .product-title .dash { width: 40px; height: 3px; background: var(--text-light); }
  .roast-row {
    position: absolute; left: 0; top: 576px; width: 100%;
    display: flex; align-items: center; justify-content: center; gap: 12px;
    color: var(--text-light);
  }
  .roast-en { font-family: "Open Sans", sans-serif; font-size: 14px; line-height: 1.05; text-align: center; }
  .roast-divider { width: 2px; height: 38px; background: var(--text-light); }
  .roast-ar { font-family: "Cairo", sans-serif; font-weight: 700; font-size: 30px; line-height: 1.1; }
  .variant-label {
    position: absolute; left: 70px; top: 630px; width: 220px; height: 40px;
    background: var(--label-red);
    display: flex; align-items: center; justify-content: center;
    font-family: "Open Sans", sans-serif; font-size: 24px; color: var(--text-light);
  }
  .net-weight {
    position: absolute; left: 0; top: 680px; width: 100%; text-align: center;
    font-family: "Open Sans", sans-serif; font-size: 15px; color: var(--text-light);
  }
</style>
</head>
<body>
<main class="canvas">
  <div class="bag">
    <aside class="bag-side">
      <div class="side-band" role="img" aria-label="Red band with gold geometric star pattern"></div>
      <div class="side-rule"></div>
      <div class="side-content">
        <p class="side-brand" lang="ar" dir="rtl">بنّيتك</p>

        <p class="side-para ar" lang="ar" dir="rtl">بن تركي محمص بعناية من أجود الحبوب المختارة.</p>
        <p class="side-para en">Freshly roasted beans, ground to order for a rich cup.</p>

        <div class="variant-group" lang="ar" dir="rtl">
          <p class="side-heading">درجة التحميص</p>
          <ul class="option-list">
            <li class="option"><span class="tick-box"></span><span>فاتح</span></li>
            <li class="option"><span class="tick-box"></span><span>وسط</span></li>
            <li class="option"><svg class="tick-box" viewBox="0 0 11 11"><path d="M2 5.5 L4.5 8 L9 2.5" fill="none" stroke="#f2f2f2" stroke-width="1.6"/></svg><span>غامق</span></li>
          </ul>
        </div>

        <div class="variant-group" lang="ar" dir="rtl">
          <p class="side-heading">النكهة</p>
          <ul class="option-list">
            <li class="option"><svg class="tick-box" viewBox="0 0 11 11"><path d="M2 5.5 L4.5 8 L9 2.5" fill="none" stroke="#f2f2f2" stroke-width="1.6"/></svg><span>سادة</span></li>
            <li class="option"><span class="tick-box"></span><span>محوج</span></li>
          </ul>
        </div>

        <div class="date-field">
          <div>
            <div class="date-row"><span class="en">PROD</span><span class="ar" lang="ar">تاريخ الإنتاج</span></div>
            <span class="date-line"></span>
          </div>
          <div>
            <div class="date-row"><span class="en">EXP</span><span class="ar" lang="ar">تاريخ الانتهاء</span></div>
            <span class="date-line"></span>
          </div>
        </div>
      </div>
    </aside>

    <section class="bag-front">
      <div class="pattern-band" role="img" aria-label="Red band with gold geometric star pattern"></div>
      <div class="gold-rule"></div>

      <h1 class="brand-name" lang="ar" dir="rtl">بنّيتك</h1>
      <p class="brand-tagline">Turkish Coffee Brand</p>

      <svg class="product-illustration" viewBox="0 0 150 155" role="img" aria-label="Brass Arabic coffee pot beside a small steaming coffee cup">
        <defs>
          <radialGradient id="brassGlow" cx="45%" cy="55%" r="60%">
            <stop offset="0%" stop-color="#d9b77c"/>
            <stop offset="100%" stop-color="#2a2a2b" stop-opacity="0"/>
          </radialGradient>
        </defs>
        <rect width="150" height="155" fill="url(#brassGlow)"/>
      </svg>

      <div class="product-title">
        <span class="dash"></span>
        <span>BINNITAK</span>
        <span class="dash"></span>
      </div>

      <div class="roast-row">
        <span class="roast-en">DARK<br>ROASTED</span>
        <span class="roast-divider"></span>
        <span class="roast-ar" lang="ar" dir="rtl">غامق</span>
      </div>

      <div class="variant-label">COFFEE BEANS</div>
      <p class="net-weight">500G</p>
    </section>
  </div>
</main>
</body>
</html>
```